BRN website video quote promotion tiles

We are promoting vehicle leasing by video, which contains several quotation examples imported from the video. We must re-vamp the quotation tiles, contact boxes, and contact form. The first tile is generated from the video, so this must be a separate project. We are looking for a welcoming, professional flow and leave color choices to design with an emphasis on communication prompts, and additional prompts in the design would be welcome.

Target Market(s)

Any Customer interaction from the tile quotes, contact, call, message,

Industry/Entity Type

vehicle leasing

Coding

Coded - Design and coding required

Number of Pages Required

1 page

Colors

Designer to choose colors to be used in the design.

Requirements
Must have
• emphasis on point of contact and visual impact on quote tile excluding main one
Should not have
• changes to the quote structure as these imported from video pricing no changes to main image as this template which can addressed as separate project

```html
<!DOCTYPE html>
<html lang="en">
<head>
<meta charset="utf-8">
<title>BRN Contract Hire Quote Tiles</title>
<link href="https://fonts.googleapis.com/css2?family=Roboto:ital,wght@0,400;0,500;0,700;0,900;1,400&display=swap" rel="stylesheet">
<style>
:root{
  --green:#7ccf6f;
  --orange:#e07f33;
  --ink:#111111;
  --price:#2b2b2b;
  --muted:#6f6f6f;
  --dark:#1a1a1a;
  --white:#ffffff;
}
*{box-sizing:border-box;margin:0;padding:0}
html,body{width:1057px;height:1200px;overflow:hidden;background:var(--white);font-family:"Roboto",Arial,sans-serif}
.canvas{position:relative;width:1057px;height:1200px}

/* Style A: framed tiles */
.tile-a{position:absolute;top:69px;width:272px;height:272px}
.tile-a .frame{position:absolute;left:-23px;top:0;width:300px;height:296px;overflow:visible}
.tile-a .card{position:absolute;inset:0;background:var(--white);border-radius:22px;box-shadow:0 6px 22px rgba(0,0,0,.08);overflow:hidden}
.tile-a .title{position:absolute;left:25px;top:26px;font-weight:900;font-size:33px;line-height:42px;color:var(--ink);letter-spacing:.5px}
.tile-a .title .rule{display:inline-block;width:112px;height:1px;background:var(--green);vertical-align:middle;margin-left:8px}
.tile-a .terms{position:absolute;left:25px;top:121px;font-size:14.5px;color:var(--orange)}
.tile-a .note{position:absolute;left:25px;top:146px;font-size:13px;font-style:italic;color:var(--muted)}
.tile-a .price{position:absolute;right:25px;top:170px;font-size:31px;font-weight:700;color:var(--price)}
.tile-a .vat{position:absolute;right:28px;top:206px;font-size:13.5px;font-style:italic;color:var(--muted)}
.tile-a .chat{position:absolute;left:0;bottom:0;width:60px;height:60px;background:var(--green);border-radius:0 20px 0 0;display:flex;align-items:center;justify-content:center;color:var(--white);font-size:11px;font-weight:700}
.tile-a .contact{position:absolute;right:25px;top:238px;font-size:14px;font-weight:700;color:var(--orange);display:flex;align-items:center;gap:10px}

/* Style B: dark band tiles */
.band{position:absolute;left:0;top:435px;width:1057px;height:388px;background:var(--dark)}
.tile-b{position:absolute;top:58px;width:273px;height:272px;background:var(--white);border-radius:24px;padding:10px 11px;text-align:center}
.tile-b .head{height:69px;border-radius:18px;background:var(--orange);position:relative;color:var(--white);font-weight:500;font-size:19px;padding-top:34px}
.tile-b .head::before{content:"";position:absolute;left:50%;top:20px;width:38px;height:3px;margin-left:-19px;border-radius:2px;background:var(--white)}
.tile-b .terms{margin-top:24px;font-size:15px;color:var(--orange)}
.tile-b .note{margin-top:12px;font-size:13.5px;font-style:italic;color:var(--muted)}
.tile-b .price{margin-top:9px;font-size:31px;font-weight:700;color:var(--price)}
.tile-b .price small{font-size:13.5px;font-weight:400;font-style:italic;color:var(--muted)}
.tile-b .actions{margin-top:9px;display:flex;justify-content:space-between;padding:0 2px}
.btn{display:flex;align-items:center;justify-content:center;width:119px;height:34px;border-radius:17px;font-size:14px;font-weight:700;color:var(--white)}
.btn.chat{background:var(--green)}
.btn.contact{background:var(--orange)}
.tile-b.featured{background:var(--green)}
.tile-b.featured .head{background:var(--white);color:var(--orange)}
.tile-b.featured .head::before{background:var(--orange)}
.tile-b.featured .terms,.tile-b.featured .note,.tile-b.featured .price,.tile-b.featured .price small{color:var(--white)}
.tile-b.featured .btn.chat{background:var(--white);color:var(--green)}

/* Style C: icon badge tiles */
.tile-c{position:absolute;top:873px;width:272px;height:258px;background:var(--white);border-radius:22px;box-shadow:0 4px 20px rgba(0,0,0,.07)}
.tile-c .badge{position:absolute;left:-31px;top:22px;width:67px;height:67px;border-radius:50%;background:var(--green);display:flex;align-items:center;justify-content:center}
.tile-c .title{position:absolute;left:51px;top:27px;font-size:23px;font-weight:500;color:var(--ink)}
.tile-c .terms{position:absolute;left:51px;top:59px;width:180px;font-size:15px;line-height:24px;color:var(--orange)}
.tile-c .note{position:absolute;left:49px;top:118px;font-size:13.5px;font-style:italic;color:var(--muted)}
.tile-c .price{position:absolute;left:48px;top:144px;font-size:31px;font-weight:700;color:var(--price)}
.tile-c .price small{font-size:13.5px;font-weight:400;font-style:italic;color:var(--muted)}
.tile-c .actions{position:absolute;left:13px;right:13px;top:202px;display:flex;justify-content:space-between}
</style>
</head>
<body>
<div class="canvas">

  <!-- Row 1 -->
  <section class="tile-a" style="left:67px">
    <svg class="frame" viewBox="0 0 300 296" aria-hidden="true">
      <path d="M2 0 V110" stroke="#7ccf6f" stroke-width="2" fill="none"/>
      <path d="M2 110 V262 Q2 294 34 294 H210" stroke="#7ccf6f" stroke-width="4" fill="none"/>
      <path d="M210 294 H300" stroke="#7ccf6f" stroke-width="2" fill="none"/>
    </svg>
    <div class="card">
      <h2 class="title">CONTRACT<br>HIRE<span class="rule"></span></h2>
      <p class="terms">3 years, 9+35, 10k miles annually</p>
      <p class="note">* Not Maintained</p>
      <p class="price">€247.33</p>
      <p class="vat">Plus VAT</p>
      <span class="chat">ChatLine</span>
      <span class="contact"><svg width="14" height="14" viewBox="0 0 14 14" fill="none" stroke="#e07f33" stroke-width="1.6"><path d="M6 2H2v10h10V8"/><path d="M5 9l1-3 6-5 2 2-6 5z"/></svg>CONTACT US</span>
    </div>
  </section>
  <section class="tile-a" style="left:401px">
    <svg class="frame" viewBox="0 0 300 296" aria-hidden="true">
      <path d="M2 0 V110" stroke="#7ccf6f" stroke-width="2" fill="none"/>
      <path d="M2 110 V262 Q2 294 34 294 H210" stroke="#7ccf6f" stroke-width="4" fill="none"/>
      <path d="M210 294 H300" stroke="#7ccf6f" stroke-width="2" fill="none"/>
    </svg>
    <div class="card">
      <h2 class="title">CONTRACT<br>HIRE<span class="rule"></span></h2>
      <p class="terms">3 years, 9+35, 10k miles annually</p>
      <p class="note">* Not Maintained</p>
      <p class="price">€247.33</p>
      <p class="vat">Plus VAT</p>
      <span class="chat">ChatLine</span>
      <span class="contact"><svg width="14" height="14" viewBox="0 0 14 14" fill="none" stroke="#e07f33" stroke-width="1.6"><path d="M6 2H2v10h10V8"/><path d="M5 9l1-3 6-5 2 2-6 5z"/></svg>CONTACT US</span>
    </div>
  </section>
  <section class="tile-a" style="left:735px">
    <svg class="frame" viewBox="0 0 300 296" aria-hidden="true">
      <path d="M2 0 V110" stroke="#7ccf6f" stroke-width="2" fill="none"/>
      <path d="M2 110 V262 Q2 294 34 294 H210" stroke="#7ccf6f" stroke-width="4" fill="none"/>
      <path d="M210 294 H300" stroke="#7ccf6f" stroke-width="2" fill="none"/>
    </svg>
    <div class="card">
      <h2 class="title">CONTRACT<br>HIRE<span class="rule"></span></h2>
      <p class="terms">3 years, 9+35, 10k miles annually</p>
      <p class="note">* Not Maintained</p>
      <p class="price">€247.33</p>
      <p class="vat">Plus VAT</p>
      <span class="chat">ChatLine</span>
      <span class="contact"><svg width="14" height="14" viewBox="0 0 14 14" fill="none" stroke="#e07f33" stroke-width="1.6"><path d="M6 2H2v10h10V8"/><path d="M5 9l1-3 6-5 2 2-6 5z"/></svg>CONTACT US</span>
    </div>
  </section>

  <!-- Row 2 -->
  <div class="band">
    <section class="tile-b" style="left:81px">
      <h2 class="head">CONTRACT HIRE</h2>
      <p class="terms">3 years, 9+35, 10k miles annually</p>
      <p class="note">* Not Maintained</p>
      <p class="price">€247.33 <small>Plus VAT</small></p>
      <div class="actions"><span class="btn chat">ChatLine</span><span class="btn contact">Contact Us</span></div>
    </section>
    <section class="tile-b featured" style="left:393px">
      <h2 class="head">CONTRACT HIRE</h2>
      <p class="terms">3 years, 9+35, 10k miles annually</p>
      <p class="note">* Not Maintained</p>
      <p class="price">€247.33 <small>Plus VAT</small></p>
      <div class="actions"><span class="btn chat">ChatLine</span><span class="btn contact">Contact Us</span></div>
    </section>
    <section class="tile-b" style="left:704px">
      <h2 class="head">CONTRACT HIRE</h2>
      <p class="terms">3 years, 9+35, 10k miles annually</p>
      <p class="note">* Not Maintained</p>
      <p class="price">€247.33 <small>Plus VAT</small></p>
      <div class="actions"><span class="btn chat">ChatLine</span><span class="btn contact">Contact Us</span></div>
    </section>
  </div>

  <!-- Row 3 -->
  <section class="tile-c" style="left:81px">
    <span class="badge"><svg width="34" height="34" viewBox="0 0 34 34" fill="none" stroke="#fff" stroke-width="2"><path d="M22 5H7v24h17V17"/><path d="M11 12h8M11 17h6M11 22h5"/><path d="M18 24l1-4 9-9 3 3-9 9z"/></svg></span>
    <h2 class="title">CONTRACT HIRE</h2>
    <p class="terms">3 years, 9+35, 10k miles annually</p>
    <p class="note">* Not Maintained</p>
    <p class="price">€247.33 <small>Plus VAT</small></p>
    <div class="actions"><span class="btn chat">ChatLine</span><span class="btn contact">Contact Us</span></div>
  </section>
  <section class="tile-c" style="left:412px">
    <span class="badge"><svg width="34" height="34" viewBox="0 0 34 34" fill="none" stroke="#fff" stroke-width="2"><path d="M22 5H7v24h17V17"/><path d="M11 12h8M11 17h6M11 22h5"/><path d="M18 24l1-4 9-9 3 3-9 9z"/></svg></span>
    <h2 class="title">CONTRACT HIRE</h2>
    <p class="terms">3 years, 9+35, 10k miles annually</p>
    <p class="note">* Not Maintained</p>
    <p class="price">€247.33 <small>Plus VAT</small></p>
    <div class="actions"><span class="btn chat">ChatLine</span><span class="btn contact">Contact Us</span></div>
  </section>
  <section class="tile-c" style="left:743px">
    <span class="badge"><svg width="34" height="34" viewBox="0 0 34 34" fill="none" stroke="#fff" stroke-width="2"><path d="M22 5H7v24h17V17"/><path d="M11 12h8M11 17h6M11 22h5"/><path d="M18 24l1-4 9-9 3 3-9 9z"/></svg></span>
    <h2 class="title">CONTRACT HIRE</h2>
    <p class="terms">3 years, 9+35, 10k miles annually</p>
    <p class="note">* Not Maintained</p>
    <p class="price">€247.33 <small>Plus VAT</small></p>
    <div class="actions"><span class="btn chat">ChatLine</span><span class="btn contact">Contact Us</span></div>
  </section>

</div>
</body>
</html>
```